Business card for a Exhibition booth fabrication company

Hi. My company would like to change our corporate name card. We are an events and Exhibition stand builder company. We would like our corporate name card to resonate what we do. I need someone to create something unique that relates to the industry that I am in. The graphic designer should be creative to incorporate the elements of my industry and try to blend in well in the design of the card. Our aim is to ensure that we are unique and our card can look different from our competitors.
Updates

Target Market(s)

Marketing and events manager from all companies

Contact Information for Business Card

The business card should have the following details:
Name
Job Title
Email
Website

Colors

Designer to choose colors to be used in the design.

Requirements
Must have
• The card must be look something that is relevant to the service that I am providing. My website is: www.velmora-buildworks.com
• You can see my website to get more information on what service that I am doing
Nice to have
• On the back of my card, I would like to have a globe image with the incorporation of my company logo. This is to indicate that my services can be done in any part of the world.

```html
<!DOCTYPE html>
<html lang="en">
<head>
<meta charset="utf-8">
<title>Velmora Buildworks – Business Card</title>
<link rel="stylesheet" href="https://fonts.googleapis.com/css2?family=Jost:wght@400;500;600&display=swap">
<style>
  :root {
    --stage: #3a3a3c;
    --stage-dark: #1f1f21;
    --card-black: #0c0c0d;
    --card-white: #ffffff;
    --brand-red: #e5212a;
    --ink: #1a1a1a;
    --wordmark-grey: #5a5a5c;
    --wordmark-light: #8a8a8c;
  }
  * { box-sizing: border-box; margin: 0; padding: 0; }
  html, body { width: 1200px; height: 1000px; overflow: hidden; }
  body {
    background: radial-gradient(ellipse at 50% 40%, var(--stage) 0%, var(--stage-dark) 100%);
    font-family: "Jost", sans-serif;
    position: relative;
  }
  .card {
    position: absolute;
    width: 700px;
    height: 400px;
    border-radius: 26px;
    overflow: hidden;
  }
  /* Back of card */
  .card-back {
    left: 410px; top: 50px;
    background: var(--card-black);
  }
  .card-back .globe-area {
    position: absolute;
    inset: 40px;
    border-radius: 12px;
    background: radial-gradient(ellipse at 50% 45%, #2a2a2c 0%, #161617 55%, var(--card-black) 100%);
  }
  .card-back .wordmark {
    position: absolute;
    left: 0; right: 0; top: 178px;
    text-align: center;
    font-size: 34px;
    font-weight: 500;
    letter-spacing: 3px;
    color: var(--wordmark-light);
  }
  /* Front of card */
  .card-front {
    left: 90px; top: 520px;
    background: var(--card-white);
    color: var(--ink);
  }
  .front-brand {
    position: absolute;
    left: 36px; top: 124px;
    width: 320px;
    text-align: center;
    font-size: 23px;
    font-weight: 500;
    letter-spacing: 2px;
    color: var(--wordmark-grey);
    white-space: nowrap;
  }
  .divider {
    position: absolute;
    left: 380px; top: 40px;
    width: 2px; height: 200px;
    background: var(--brand-red);
  }
  .contact {
    position: absolute;
    left: 400px; top: 38px;
    width: 260px;
    font-size: 16px;
    line-height: 1.2;
  }
  .contact .person-name { color: var(--brand-red); font-size: 25px; font-weight: 500; }
  .contact .person-title { font-size: 15px; font-weight: 500; margin-bottom: 12px; }
  .contact .region { color: var(--brand-red); font-size: 15px; }
  .contact .phone { font-size: 18px; font-weight: 500; margin-bottom: 4px; }
  .contact .line { display: flex; align-items: center; gap: 7px; font-size: 16px; font-weight: 500; margin-top: 4px; white-space: nowrap; }
  .contact .line svg { width: 15px; height: 15px; flex: none; }
  .contact .accent { color: var(--brand-red); }
  .services {
    position: absolute;
    left: 30px; right: 30px; top: 272px;
    text-align: center;
  }
  .services h2 {
    color: var(--brand-red);
    font-size: 18px;
    font-weight: 500;
    margin-bottom: 4px;
  }
  .services p {
    font-size: 15px;
    line-height: 1.3;
  }
</style>
</head>
<body>

  <section class="card card-back">
    <div class="globe-area" role="img" aria-label="Faint world map with glowing connection lines linking continents"></div>
    <div class="wordmark">VELMORA BUILDWORKS</div>
  </section>

  <section class="card card-front">
    <div class="front-brand">VELMORA BUILDWORKS</div>
    <div class="divider"></div>

    <div class="contact">
      <div class="person-name">Daniel Reyes</div>
      <div class="person-title">President</div>
      <div class="region">Singapore Contact:</div>
      <div class="phone">+65 9184 2270</div>
      <div class="region">Qatar Contact:</div>
      <div class="phone">+974 6652 0419</div>
      <div class="line">
        <svg viewBox="0 0 16 16" aria-hidden="true"><rect x="1" y="3" width="14" height="10" rx="1.5" fill="var(--brand-red)"/><path d="M1.5 4 L8 9 L14.5 4" stroke="#fff" stroke-width="1.4" fill="none"/></svg>
        <span>info@velmora-buildworks.com</span>
      </div>
      <div class="line">
        <svg viewBox="0 0 16 16" aria-hidden="true"><circle cx="8" cy="8" r="7" fill="var(--brand-red)"/><path d="M1 8 H15 M8 1 C4 5 4 11 8 15 M8 1 C12 5 12 11 8 15" stroke="#fff" stroke-width="1" fill="none"/></svg>
        <span>www.<span class="accent">velmora-buildworks</span>.com</span>
      </div>
    </div>

    <div class="services">
      <h2>OUR SERVICES</h2>
      <p>Exhibition Booth Fabrication | Outdoor Booth Setup | Interior Design | Installation and Dismantle | Exhibition Management | Shell Scheme Display Booth | Custom Stand Design | Exhibition Furniture and Equipment | Exhibition Project Management</p>
    </div>
  </section>

</body>
</html>
```